New Website for novelty yarn producer

We need a new website for our company, Vedrana. We make highly tailored yarns for weavers worldwide. This year marks our 40th anniversary and we want to evolve our image and identity.

Our temporary website can be found at:
www.vedranathreads.example

Our only concern in that throughout the website the protagonist must be our client, we make their creations possible and are highly adaptable both during the ideation process of the yarn as well as in the production. This is at the core of the way we do business and is summarised within the concept of FMC (Full Motion Craft).

Industry/Entity Type

Textile

Number of Pages Required

1 page

Colors
9bcb3c

Requirements
Must have
• Full Motion Craft (FMC) - can be found on or current website www.vedranathreads.example

```html
<!DOCTYPE html>
<html lang="en">
<head>
<meta charset="utf-8">
<title>Vedrana – Tailored Weaving Solutions</title>
<link href="https://fonts.googleapis.com/css2?family=Open+Sans:wght@400;600&family=Roboto+Condensed:wght@400;700&display=swap" rel="stylesheet">
<style>
:root{
  --green:#4aa53a;
  --green-light:#9bcb3c;
  --ink:#1d1d1d;
  --text:#555;
  --muted:#f0f0f0;
  --band:#ececec;
  --footer:#0f0f0f;
  --footer-bottom:#060606;
  --white:#fff;
}
*{box-sizing:border-box;margin:0;padding:0}
html,body{width:1200px;height:2830px;overflow:hidden;background:var(--white)}
body{font-family:"Open Sans",sans-serif;color:var(--text);position:relative}
.abs{position:absolute}
.heading{font-family:"Roboto Condensed",sans-serif;color:var(--ink);font-weight:400}

/* hero */
.hero-bg{left:0;top:0;width:1200px;height:615px;background:linear-gradient(100deg,#3a1a16 0%,#5a2a24 25%,#2f2a26 55%,#3b3d3c 80%,#2a2c2b 100%)}
.topbar{left:90px;top:0;width:1023px;height:82px;background:#ececec;display:flex;align-items:center;padding:0 22px}
.brand{font-family:"Roboto Condensed",sans-serif;font-weight:700;font-size:34px;color:var(--ink);letter-spacing:1px}
.nav{display:flex;gap:38px;margin-left:auto;margin-right:36px;font-size:15px;color:#222}
.nav .active{color:var(--green)}
.badge{left:546px;top:98px;width:108px;height:108px;border:2px solid var(--white);border-radius:50%;color:var(--white);text-align:center;font-family:"Roboto Condensed",sans-serif}
.badge .num{font-size:40px;line-height:40px;margin-top:20px}
.badge .name{font-size:14px}
.hero-title{left:0;top:210px;width:1200px;text-align:center;color:var(--white);font-size:39px;font-family:"Roboto Condensed",sans-serif}
.hero-media{left:155px;top:282px;width:890px;height:440px;border:4px solid #f4f4f4;box-shadow:0 24px 28px rgba(0,0,0,.35);background:linear-gradient(110deg,#3c5a2a 0%,#7ea63a 30%,#9cab6e 50%,#7f9aa6 72%,#4d6a8c 100%)}
.play{width:64px;height:64px;border-radius:50%;background:rgba(30,30,30,.85);display:flex;align-items:center;justify-content:center}

/* features */
.section-title{left:0;top:808px;width:1200px;text-align:center;font-size:37px}
.feature{top:915px;width:300px;text-align:center}
.feature .icon{width:106px;height:106px;border:1.5px solid #4b5b6a;border-radius:50%;margin:0 auto;display:flex;align-items:center;justify-content:center}
.feature h3{font-size:26px;margin-top:20px}
.feature p{font-size:14px;line-height:23px;margin-top:12px;padding:0 18px}
.feature .more{display:block;font-size:14px;color:#222;margin-top:14px}

/* production */
.production-bg{left:0;top:1280px;width:1200px;height:485px;background:linear-gradient(90deg,#262626,#3a3a3a 50%,#2b2b2b)}
.production-card{left:137px;top:1368px;width:528px;height:327px;background:var(--white);padding:34px 48px}
.production-card h2{font-size:30px}
.production-card p{font-size:14px;line-height:23px;margin-top:14px;text-align:justify;color:#444}
.btn-outline{display:inline-block;border:2px solid var(--green);border-radius:18px;color:var(--green);font-size:12px;font-weight:600;padding:6px 18px;text-transform:uppercase}
.production-media{left:665px;top:1368px;width:390px;height:327px;background:linear-gradient(135deg,#8b8b8b,#4a4a4a 50%,#2a2a2a)}
.fmc-label{left:212px;top:218px;color:var(--white);font-size:16px;line-height:20px;border-left:1px solid var(--white);padding-left:12px;text-transform:uppercase}

/* numbers */
.numbers-bg{left:0;top:1765px;width:1200px;height:300px;background:var(--band)}
.numbers-title{left:98px;top:1842px;font-size:38px}
.numbers-year{left:98px;top:1892px;font-size:29px;color:#333}
.btn-fill{left:98px;top:1942px;width:148px;height:34px;border-radius:17px;background:var(--green);color:var(--white);font-size:12.5px;font-weight:600;display:flex;align-items:center;justify-content:center;text-transform:uppercase}
.stat{top:1832px;width:260px;text-align:center}
.stat .ring{width:122px;height:122px;margin:0 auto;border:5px solid var(--green);border-radius:50%;background:#e0e0e0;display:flex;align-items:center;justify-content:center;font-family:"Roboto Condensed",sans-serif;font-size:40px;color:#333}
.stat .label{font-size:19px;color:#222;margin-top:12px;font-weight:600}

/* heritage */
.heritage-frame{left:118px;top:2152px;width:392px;height:268px;border:2px solid var(--green)}
.heritage-media{left:140px;top:2172px;width:405px;height:268px;background:linear-gradient(160deg,#5a6b86,#8a8fa0 40%,#8c9a5a 75%,#6d7a3c)}
.heritage-text{left:588px;top:2172px;width:460px}
.heritage-text h2{font-size:29px;text-transform:uppercase}
.heritage-text p{font-size:14px;line-height:23px;margin-top:12px;text-align:justify;color:#444}

/* footer */
.footer{left:0;top:2530px;width:1200px;height:220px;background:var(--footer);color:var(--white)}
.footer .company{left:92px;top:42px}
.footer .company h4{font-size:17px;font-weight:600}
.footer .company p{font-size:12px;line-height:22px;margin-top:4px}
.footer .brand-mark{left:0;top:82px;width:1200px;text-align:center;font-family:"Roboto Condensed",sans-serif;font-weight:700;font-size:34px;letter-spacing:1px;color:var(--white)}
.newsletter{left:808px;top:52px}
.newsletter h4{font-size:17px;font-weight:600}
.newsletter .field{margin-top:14px;width:304px;height:50px;border:1px solid #bbb;border-radius:4px;display:flex;font-size:12px}
.newsletter .field span:first-child{flex:1;padding:17px 12px}
.newsletter .field span:last-child{border-left:1px solid #bbb;padding:17px 16px}
.copyright{left:0;top:2750px;width:1200px;height:80px;background:var(--footer-bottom);color:var(--white);font-size:13px;display:flex;align-items:center;justify-content:center}
</style>
</head>
<body>

<div class="abs hero-bg" role="img" aria-label="Close-up photograph of colourful wound yarn"></div>
<header class="abs topbar">
  <span class="brand">VEDRANA</span>
  <nav class="nav"><span class="active">Home</span><span>About us</span><span>Full Motion Craft</span><span>More...</span></nav>
  <svg width="20" height="20" viewBox="0 0 20 20"><circle cx="8" cy="8" r="6" fill="none" stroke="#111" stroke-width="2.5"/><line x1="12.5" y1="12.5" x2="18" y2="18" stroke="#111" stroke-width="3"/></svg>
</header>
<div class="abs badge"><div class="num">40</div><div class="name">VEDRANA</div></div>
<h1 class="abs hero-title">TAILORED WEAVING SOLUTIONS</h1>
<div class="abs hero-media" role="img" aria-label="Video still of woven fabric swatches in greens and blues">
  <div class="play abs" style="left:409px;top:184px"><svg width="24" height="26"><polygon points="4,2 22,13 4,24" fill="#fff"/></svg></div>
</div>

<h2 class="abs heading section-title">Our Features</h2>
<div class="abs feature" style="left:130px">
  <div class="icon"><svg width="50" height="44" viewBox="0 0 50 44" fill="var(--green)"><circle cx="25" cy="10" r="7"/><circle cx="10" cy="14" r="5"/><circle cx="40" cy="14" r="5"/><path d="M13 40 q0-18 12-18 q12 0 12 18z"/><path d="M1 36 q0-14 9-14 q4 0 5 2 q-4 5-4 12z"/><path d="M49 36 q0-14-9-14 q-4 0-5 2 q4 5 4 12z"/></svg></div>
  <h3 class="heading">Experience</h3>
  <p>Over the years the company has gained the knowledge and skills that define the superiority</p>
  <span class="more">Learn More -&gt;</span>
</div>
<div class="abs feature" style="left:453px">
  <div class="icon"><svg width="52" height="46" viewBox="0 0 52 46"><circle cx="18" cy="26" r="11" fill="none" stroke="var(--green)" stroke-width="8" stroke-dasharray="5 3.6"/><circle cx="18" cy="26" r="4" fill="var(--green)"/><circle cx="39" cy="12" r="7" fill="none" stroke="var(--green)" stroke-width="6" stroke-dasharray="3.5 2.5"/><circle cx="40" cy="36" r="6" fill="none" stroke="var(--green)" stroke-width="5" stroke-dasharray="3 2"/></svg></div>
  <h3 class="heading">Creativity</h3>
  <p>Our belief is that the key to our clients' success is a combination of innovation, creativity and quality.</p>
  <span class="more">Learn More -&gt;</span>
</div>
<div class="abs feature" style="left:768px">
  <div class="icon"><svg width="56" height="36" viewBox="0 0 56 36" fill="var(--green)"><rect x="0" y="6" width="9" height="20" rx="2"/><rect x="47" y="6" width="9" height="20" rx="2"/><path d="M10 8 l12-4 l8 4 l-10 8 q4 4 10-2 l8 6 l8-2 v10 l-6 4 l-18 4 l-12-10z"/></svg></div>
  <h3 class="heading">Professionality</h3>
  <p>We are a family business at the core. Our company is run with the same values as the Bellandi family:</p>
  <span class="more">Learn More -&gt;</span>
</div>

<div class="abs production-bg" role="img" aria-label="Photograph of dark knitted fabric with loose yellow yarn"></div>
<section class="abs production-card">
  <h2 class="heading">Production built around you</h2>
  <p>We believe that the key to delivering a yarn that exceeds our client's expectation is to work together with weavers from step one, starting from the desired end product and working backwards. This allows us to develop the product that our weavers need, rather than having weavers adapt to the supplied raw materials. Our Full Motion Craft consists achieving maximum flexibility both in development.</p>
  <span class="btn-outline" style="margin-top:16px">Read More</span>
</section>
<div class="abs production-media" role="img" aria-label="Video still of a yarn spinning machine">
  <div class="play abs" style="left:163px;top:100px"><svg width="24" height="26"><polygon points="4,2 22,13 4,24" fill="#fff"/></svg></div>
  <div class="abs fmc-label">Full<br>Motion<br>Craft</div>
</div>

<div class="abs numbers-bg"></div>
<h2 class="abs heading numbers-title">VTS in Numbers</h2>
<div class="abs heading numbers-year">2017</div>
<div class="abs btn-fill">Find out more</div>
<div class="abs stat" style="left:415px"><div class="ring">40</div><div class="label">Years in business</div></div>
<div class="abs stat" style="left:678px"><div class="ring">02</div><div class="label">Million kilograms/ yr</div></div>
<div class="abs stat" style="left:895px"><div class="ring">08</div><div class="label">Brands</div></div>

<div class="abs heritage-frame"></div>
<div class="abs heritage-media" role="img" aria-label="Photograph of stacked textured fabric samples"></div>
<section class="abs heritage-text">
  <h2 class="heading">Heritage</h2>
  <p>Our team has decades of experience in providing yarn solutions to weavers around the world, assisting them in the creation of outstanding textiles.</p>
  <p>Our clients can expect open lines of communication, clarity and professionality</p>
  <p>Our focus is our client. The success of a client is our success.</p>
  <span class="btn-outline" style="margin-top:16px">Our Heritage</span>
</section>

<footer class="abs footer">
  <div class="abs company">
    <h4>Tessiroma s.r.l</h4>
    <p>Via dei Telai 12 - 50100 Colleverde -<br>Italy - Tel. 0555 010203 r.a. - Fax 0555 010299<br>R.E.A CV 100200- Reg. Imp. CV 01234567890<br>P. IVA 09876543210 - Cod. Fisc. 01234567890<br>Capitale sociale € 80. 000, 00 int. ver.</p>
  </div>
  <div class="abs brand-mark">VEDRANA</div>
  <div class="abs newsletter">
    <h4>Sign up for newsletter</h4>
    <div class="field"><span>Your email here</span><span>Subscribe</span></div>
  </div>
</footer>
<div class="abs copyright">Copyright © 2018. All Rights Reserved</div>

</body>
</html>
```